Business Card Design - ChoiceCraft

Looking for creative, modern design, two sided for ChoiceCraft that is consistent with color and feel of website www.choicecraftpro.net.
Updates

Back of card will be used to promote products or have a quote revolving around decisions, change, leadership, innovation, creativity. Back should also have space to promote website, but optional to use the icon. Front of the card will need to use the icon and have standard place for name, job title, phone and email. We are not looking to put a mailing address or fax. Also want space to place a few words/phrase explaining what we do...such as individual growth and organizational development or tools, training, information...in addition, want the facebook icon small on the front somewhere as we are also on facebook.

Vector file uploaded of icon.

Target Market(s)

Professional coaching for individual growth and organizational development

Industry/Entity Type

Business

Requirements
Must have
• Icon...see attached.

```html
<!DOCTYPE html>
<html lang="en">
<head>
<meta charset="utf-8">
<title>ChoiceCraft Business Card</title>
<link rel="stylesheet" href="https://fonts.googleapis.com/css2?family=Tinos:wght@400;700&family=Arimo:wght@400;700&display=swap">
<style>
  :root {
    --page: #e6e7e9;
    --card: #ffffff;
    --ink: #222222;
    --navy: #1b3a78;
    --navy-deep: #14295a;
    --sky: #2fa9e3;
    --sky-light: #7fd0f2;
    --accent: #2a93cf;
    --divider: #cfd3d8;
    --mark: #4a8fd0;
  }
  * { margin: 0; padding: 0; box-sizing: border-box; }
  html, body { width: 1200px; height: 1076px; overflow: hidden; background: var(--page); }
  .canvas { position: relative; width: 1200px; height: 1076px; }

  .card {
    position: absolute;
    background: var(--card);
    border-radius: 23px;
    overflow: hidden;
    box-shadow: 0 2px 6px rgba(0,0,0,.25);
  }
  .card-front { left: 51px; top: 61px; width: 806px; height: 461px; }
  .card-back  { left: 341px; top: 557px; width: 798px; height: 456px; }

  /* front */
  .brand-mark {
    position: absolute; left: 147px; top: 72px; width: 178px; height: 178px;
    border-radius: 50%;
    background: radial-gradient(circle at 45% 40%, #eef3fb, #9fb3cf 70%, #6d86ad);
  }
  .brand-name {
    position: absolute; left: 0; width: 472px; top: 292px; text-align: center;
    font-family: "Tinos", "Times New Roman", serif; font-weight: 700; font-size: 35px;
    color: var(--ink);
  }
  .divider { position: absolute; left: 405px; top: 123px; width: 2px; height: 196px; background: var(--divider); }
  .contact-list {
    position: absolute; left: 439px; top: 130px; list-style: none;
    font-family: "Tinos", "Times New Roman", serif; font-size: 21px; color: var(--ink);
  }
  .contact-list li { display: flex; align-items: center; height: 28.5px; }
  .contact-list svg { width: 15px; height: 15px; margin-right: 8px; flex: none; }
  .tagline {
    position: absolute; left: 439px; top: 260px;
    font-family: "Tinos", "Times New Roman", serif; font-size: 21px; line-height: 28px; color: var(--ink);
  }
  .bands { position: absolute; left: 0; top: 380px; width: 806px; height: 81px; }
  .name-line {
    position: absolute; left: 495px; top: 410px;
    font-family: "Tinos", "Times New Roman", serif; color: #fff;
  }
  .name-line .person { font-weight: 700; font-size: 27px; }
  .name-line .title { font-size: 20px; }

  /* back */
  .back-mark {
    position: absolute; left: 325px; top: 30px; width: 360px; height: 360px;
    border-radius: 50%; background: rgba(74,143,208,.08);
  }
  .quote-list { position: absolute; left: 0; top: 0; list-style: none; font-family: "Arimo", Arial, sans-serif; }
  .quote { position: absolute; left: 32px; display: flex; }
  .quote-dot {
    width: 28px; height: 28px; border-radius: 50%; flex: none; margin-top: 10px;
    background: radial-gradient(circle at 45% 40%, #e4edf9, var(--mark) 75%);
  }
  .quote-body { margin-left: 14px; position: relative; }
  .quote-text { font-size: 21px; color: var(--ink); white-space: nowrap; padding-left: 26px; position: relative; }
  .quote-text::before {
    content: "\201C"; position: absolute; left: 0; top: -6px;
    font-family: "Tinos", serif; font-weight: 700; font-size: 34px; color: #333;
  }
  .quote-text::after {
    content: "\201D"; font-family: "Tinos", serif; font-weight: 700; font-size: 34px; color: #333;
    position: relative; top: 12px; margin-left: 2px; line-height: 0;
  }
  .quote-author { font-size: 21px; color: var(--ink); padding-left: 26px; margin-top: 9px; }
  .quote-author strong { color: var(--accent); }
</style>
</head>
<body>
<main class="canvas">

  <section class="card card-front">
    <div class="brand-mark" role="img" aria-label="ChoiceCraft brand icon area"></div>
    <div class="brand-name">ChoiceCraft</div>
    <div class="divider"></div>
    <ul class="contact-list">
      <li><svg viewBox="0 0 16 16"><path d="M4 1.5l2.5 3-1.5 1.7c.8 1.8 2.2 3.2 4 4l1.7-1.5 3 2.5-1.5 2.5C6.7 13.4 2.6 9.3 1.5 3z" fill="none" stroke="#222" stroke-width="1.5"/></svg>555-210-487</li>
      <li><svg viewBox="0 0 16 16"><rect x="1" y="3" width="14" height="10" fill="#222"/><path d="M1.5 3.5L8 9l6.5-5.5" fill="none" stroke="#fff" stroke-width="1.3"/></svg>info@choicecraftpro.net</li>
      <li><svg viewBox="0 0 16 16"><circle cx="8" cy="8" r="6.5" fill="none" stroke="#222" stroke-width="1.4"/><ellipse cx="8" cy="8" rx="2.8" ry="6.5" fill="none" stroke="#222" stroke-width="1.2"/><path d="M1.5 8h13" stroke="#222" stroke-width="1.2"/></svg>www.choicecraftpro.net</li>
      <li><svg viewBox="0 0 16 16"><rect x="1.5" y="1.5" width="13" height="13" rx="2" fill="#3b5b9a"/></svg>/choicecraftpro</li>
    </ul>
    <p class="tagline">Supporting individual growth<br>and organizational development.</p>
    <svg class="bands" viewBox="0 0 806 81" preserveAspectRatio="none">
      <defs>
        <linearGradient id="skyBand" x1="0" x2="1">
          <stop offset="0" stop-color="var(--sky-light)"/>
          <stop offset="1" stop-color="var(--sky)"/>
        </linearGradient>
        <linearGradient id="navyBand" x1="0" x2="1">
          <stop offset="0" stop-color="var(--navy-deep)"/>
          <stop offset="1" stop-color="var(--navy)"/>
        </linearGradient>
      </defs>
      <polygon points="0,14 437,14 415,34 0,34" fill="url(#skyBand)"/>
      <polygon points="450,10 806,10 806,81 0,81 0,44 416,44" fill="url(#navyBand)"/>
    </svg>
    <div class="name-line"><span class="person">Your Name,</span> <span class="title">Title</span></div>
  </section>

  <section class="card card-back">
    <div class="back-mark" role="img" aria-label="Faint ChoiceCraft icon backdrop"></div>
    <ul class="quote-list">
      <li class="quote" style="top:40px"><span class="quote-dot"></span><div class="quote-body"><p class="quote-text">Try not to become a man of success, but rather a man of value.</p><p class="quote-author">- <strong>Arthur Ellison</strong></p></div></li>
      <li class="quote" style="top:121px"><span class="quote-dot"></span><div class="quote-body"><p class="quote-text">The only constant is change.</p><p class="quote-author">- <strong>Helena Corvin</strong></p></div></li>
      <li class="quote" style="top:202px"><span class="quote-dot"></span><div class="quote-body"><p class="quote-text">We are what we repeatedly do. Excellence is not an act, it is a habit.</p><p class="quote-author">- <strong>Marcus Teller</strong></p></div></li>
      <li class="quote" style="top:283px"><span class="quote-dot"></span><div class="quote-body"><p class="quote-text">Simplicity is the ultimate sophistication.</p><p class="quote-author">- <strong>Lionel Varga</strong></p></div></li>
      <li class="quote" style="top:364px"><span class="quote-dot"></span><div class="quote-body"><p class="quote-text">Life is not fair - get used to it.</p><p class="quote-author">- <strong>Bernard Gale</strong></p></div></li>
    </ul>
  </section>

</main>
</body>
</html>
```